Harborline Auto LLC

Car Dealer Customer Service
Address: 2874 Cresthaven Road, Shelbyville, TN 37162
web: www.harborlineautoxq.net
email: harborlineautoxq@mailnest.example
Phone: (931) 555-0148
Phone: (629) 555-0173

```html
<!DOCTYPE html>
<html lang="en">
<head>
<meta charset="utf-8">
<title>Harborline Auto LLC – Business Card</title>
<link href="https://fonts.googleapis.com/css2?family=Poppins:wght@400;500;600;700&display=swap" rel="stylesheet">
<style>
  :root {
    --page-bg: #e9e6e2;
    --card-bg: #f7f8f8;
    --brand-blue: #1f6e94;
    --brand-gold: #e5a93a;
    --text-dark: #2a2a2a;
    --band-text: #e8eef2;
  }
  * { margin: 0; padding: 0; box-sizing: border-box; }
  html, body {
    width: 1200px; height: 1054px; overflow: hidden;
    background: var(--page-bg);
    font-family: "Poppins", sans-serif;
  }
  .card {
    position: absolute; left: 100px; top: 227px;
    width: 1000px; height: 600px;
    background: var(--card-bg);
    border-radius: 24px; overflow: hidden;
    box-shadow: 0 10px 40px rgba(0,0,0,.12);
  }
  .brand-dot {
    position: absolute; left: 40px; top: 80px;
    width: 160px; height: 160px; border-radius: 50%;
    background: var(--brand-gold);
  }
  .brand-name {
    position: absolute; left: 232px; top: 120px;
    font-size: 58px; font-weight: 700; letter-spacing: 1px;
    color: var(--brand-blue); line-height: 1;
  }
  .person { position: absolute; left: 58px; top: 340px; color: var(--text-dark); }
  .person-name { font-size: 36px; font-weight: 700; color: var(--brand-blue); line-height: 1.1; }
  .person-role { font-size: 25px; margin-top: 6px; }
  .person-address { font-size: 25px; line-height: 1.4; margin-top: 38px; }
  .contacts { position: absolute; left: 493px; top: 338px; list-style: none; }
  .contacts li { display: flex; align-items: center; height: 35px; font-size: 23px; color: var(--text-dark); }
  .contacts li.phone { font-size: 26px; font-weight: 700; color: var(--brand-blue); letter-spacing: .5px; }
  .contacts svg { width: 24px; height: 24px; margin-right: 16px; flex: none; }
  .bottom-bands { position: absolute; left: 0; top: 0; }
  .band-label {
    position: absolute; left: 430px; top: 546px; width: 400px;
    font-size: 24px; font-weight: 600; color: var(--band-text); text-align: center;
  }
</style>
</head>
<body>
  <div class="card">
    <div class="brand-dot"></div>
    <div class="brand-name">HARBORLINE AUTO</div>

    <div class="person">
      <div class="person-name">Daniel Corvey</div>
      <div class="person-role">Managing Director</div>
      <div class="person-address">2874 Cresthaven Road,<br>Shelbyville, TN 37162</div>
    </div>

    <ul class="contacts">
      <li class="phone">
        <svg viewBox="0 0 24 24"><path fill="#e5a93a" d="M3 9c0-3 4-5 9-5s9 2 9 5l-4 1-1-2H8L7 10zM6 12h12l2 8H4z"/><circle cx="12" cy="15.5" r="2" fill="#f7f8f8"/></svg>
        931-555-0148
      </li>
      <li class="phone">
        <svg viewBox="0 0 24 24"><path fill="#e5a93a" d="M3 9c0-3 4-5 9-5s9 2 9 5l-4 1-1-2H8L7 10zM6 12h12l2 8H4z"/><circle cx="12" cy="15.5" r="2" fill="#f7f8f8"/></svg>
        629-555-0173
      </li>
      <li>
        <svg viewBox="0 0 24 24"><rect x="2" y="5" width="20" height="14" fill="#e5a93a"/><path d="M2 5l10 8 10-8" fill="none" stroke="#f7f8f8" stroke-width="1.6"/></svg>
        www.harborlineautoxq.net
      </li>
      <li>
        <svg viewBox="0 0 24 24"><circle cx="12" cy="12" r="10" fill="#e5a93a"/><g fill="none" stroke="#f7f8f8" stroke-width="1.3"><ellipse cx="12" cy="12" rx="4" ry="10"/><path d="M2 12h20M4 7h16M4 17h16"/></g></svg>
        harborlineautoxq@mailnest.example
      </li>
    </ul>

    <svg class="bottom-bands" width="1000" height="600" viewBox="0 0 1000 600">
      <rect x="0" y="580" width="420" height="20" fill="var(--brand-gold)"/>
      <path d="M410 533H1000V600H381z" fill="var(--brand-blue)"/>
    </svg>
    <div class="band-label">HARBORLINE AUTO LLC</div>
  </div>
</body>
</html>
```